Brintel Works - Fast, Efficient and Gas Mainteance for Domestic, Commercial and Industrial clients

We are in the process of purchasing a new business and would like to get a new logo and business card.
Business is a gas maintenance business that also does new gas installations.
Has been established since 1988.
Services include:
Install all types of gas appliances & equipment inc. hot water units
Maintain / repair / replace all types of gas appliances & equipment

Target Market(s)

Domestic, Commercial and Industrial clients

Industry/Entity Type

Business

Contact Information for Business Card

admin@brintelworks.com.au
07 3918 4726
Brintel Works PTY LTD

Logo Text

Gas Fitting & Plumbing Maintenance Specialists

Font styles to use
Sans Serif

Requirements
Must have
• Logo
• Business name, contact number, email address, web address
• Domestic | Commercial | Industrial Est Since 1988
Nice to have
• Possibly a black card with a flame logo to one side
Should not have
• Spelling errors

```html
<!DOCTYPE html>
<html lang="en">
<head>
<meta charset="utf-8">
<title>Brintel Works – Business Card</title>
<link rel="stylesheet" href="https://fonts.googleapis.com/css2?family=Montserrat:wght@400;500;700&display=swap">
<style>
  :root {
    --ink: #0a0a0a;
    --paper: #ffffff;
    --yellow: #f7ea24;
    --orange: #f05a22;
    --flame-deep: #ee5a1c;
    --flame-mid: #f6921e;
    --flame-light: #f9e11e;
    --text-dark: #1a1a1a;
    --backdrop: #dcdad7;
  }
  * { box-sizing: border-box; margin: 0; padding: 0; }
  html, body {
    width: 1200px; height: 1189px; overflow: hidden;
    background: var(--backdrop);
    font-family: "Montserrat", Arial, sans-serif;
  }
  .card {
    position: absolute; left: 160px;
    width: 880px; height: 503px;
    overflow: hidden;
    box-shadow: 0 6px 18px rgba(0,0,0,.18);
  }

  /* ---------- Back of card ---------- */
  .card-back { top: 60px; background: var(--ink); color: var(--paper); text-align: center; }
  .brand-mark {
    display: flex; align-items: center; justify-content: center; gap: 14px;
    margin-top: 46px;
  }
  .brand-mark__dot {
    width: 26px; height: 26px; border-radius: 50%; background: var(--yellow);
  }
  .brand-mark__name { font-size: 30px; font-weight: 500; letter-spacing: .5px; }
  .company-name { margin-top: 38px; font-size: 40px; font-weight: 400; letter-spacing: .5px; }
  .company-tagline { margin-top: 6px; font-size: 14px; letter-spacing: 1px; }
  .services-title { margin-top: 26px; font-size: 22px; color: var(--yellow); letter-spacing: 1px; }
  .services-list { margin-top: 8px; font-size: 19px; line-height: 1.45; letter-spacing: .4px; }
  .web-band {
    position: absolute; left: 0; right: 0; bottom: 0; height: 96px;
    background: var(--yellow); color: var(--ink);
    display: flex; align-items: center; justify-content: center;
    font-size: 20px; font-weight: 500; letter-spacing: .6px;
  }

  /* ---------- Front of card ---------- */
  .card-front { top: 626px; background: var(--paper); color: var(--text-dark); }
  .side-strip {
    position: absolute; left: 0; top: 0; bottom: 0; width: 236px;
    background: var(--ink);
    border-right: 3px solid var(--orange);
    display: flex; flex-direction: column; align-items: center;
    padding-top: 62px; gap: 12px; color: var(--paper);
  }
  .side-strip .brand-mark__dot { width: 22px; height: 22px; }
  .side-strip__name { font-size: 24px; font-weight: 500; }
  .front-heading { position: absolute; left: 270px; top: 56px; }
  .front-heading .company-name { margin-top: 0; font-size: 36px; }
  .front-heading .company-tagline { font-size: 12px; }
  .flame-art {
    position: absolute; right: -30px; top: 30px; width: 260px; height: 270px;
    border-radius: 60% 40% 20% 50%;
    background: radial-gradient(circle at 60% 70%, var(--flame-light) 0 30%, var(--flame-mid) 55%, var(--flame-deep) 80%, transparent 81%);
  }
  .contact { position: absolute; left: 290px; top: 236px; }
  .contact__person { font-size: 28px; font-weight: 700; margin-bottom: 14px; }
  .contact__line { font-size: 21px; line-height: 1.3; display: flex; align-items: center; gap: 10px; }
  .contact__icon { width: 20px; height: 20px; flex: none; }
</style>
</head>
<body>

<section class="card card-back" aria-label="Business card back">
  <div class="brand-mark">
    <span class="brand-mark__dot"></span>
    <span class="brand-mark__name">Brintel Works</span>
  </div>
  <h1 class="company-name">Brintel Works PTY LTD</h1>
  <p class="company-tagline">Domestic | Commercial | Industrial Est Since 1988</p>
  <h2 class="services-title">SERVICES</h2>
  <p class="services-list">
    Install all types of gas appliances &amp; equipment inc. hot water units<br>
    Maintain / repair / replace all types of gas appliances &amp; equipment
  </p>
  <div class="web-band">www.brintelworks.com.au</div>
</section>

<section class="card card-front" aria-label="Business card front">
  <div class="side-strip">
    <span class="brand-mark__dot"></span>
    <span class="side-strip__name">Brintel Works</span>
  </div>
  <div class="front-heading">
    <h1 class="company-name">Brintel Works PTY LTD</h1>
    <p class="company-tagline">Domestic | Commercial | Industrial Est Since 1988</p>
  </div>
  <div class="flame-art" role="img" aria-label="Illustrated orange and yellow flames"></div>
  <div class="contact">
    <p class="contact__person">Employee Name</p>
    <p class="contact__line">0000 your address Avenue</p>
    <p class="contact__line">Harlow Creek, SD 0000</p>
    <p class="contact__line">
      <svg class="contact__icon" viewBox="0 0 20 20" aria-hidden="true">
        <rect x="1" y="1" width="18" height="18" fill="var(--ink)"/>
        <path d="M6 5c-1 1-1 3 1 6s4 4 6 4l1-2-2-1-1 1c-1 0-3-2-3-3l1-1-1-2z" fill="var(--paper)"/>
      </svg>
      07 3918 4726
    </p>
    <p class="contact__line">
      <svg class="contact__icon" viewBox="0 0 20 20" aria-hidden="true">
        <rect x="1" y="1" width="18" height="18" fill="var(--ink)"/>
        <rect x="4" y="6" width="12" height="8" fill="none" stroke="var(--paper)" stroke-width="1.3"/>
        <path d="M4 6l6 5 6-5" fill="none" stroke="var(--paper)" stroke-width="1.3"/>
      </svg>
      admin@brintelworks.com.au
    </p>
  </div>
</section>

</body>
</html>
```